The Copperline Collective's website for high impact furniture promotions

I am looking for a simple website. we are a promotional company that runs events for furniture stores to increase sales for short periods of time. i would like the website to have about 4 areas to explain our company. I would like it to be simple and user friendly. I would like a link to chatterbook and a contact section. I am attaching our logo that i would like somewhere large or possibly in the backround. I am open to different color schemes. I would like to convey fast paced, modern, reliable. I am open to all different styles and look forward to seeing whats out there. we are looking for a quick turn around, so if we see one that we like quick, we will pick that one thanks
Reason: looking for some really creative designs and want to give a fair amount of time to produce
Target Market(s)
Retail Furniture store owners
Industry/Entity Type
It Company
Number of Pages Required
1 page
Colors
Designer to choose colors to be used in the design.
Look and feel

```html
<!DOCTYPE html>
<html lang="en">
<head>
<meta charset="utf-8">
<title>The Copperline Collective</title>
<link href="https://fonts.googleapis.com/css2?family=Open+Sans:ital,wght@0,400;0,600;0,700;1,400&display=swap" rel="stylesheet">
<style>
:root{
  --brown:#8b5a2b;
  --brown-dark:#6f4622;
  --tan:#c49a6c;
  --text:#333;
  --muted:#555;
  --soft:#f7f7f7;
  --line:#ddd;
  --white:#fff;
}
*{box-sizing:border-box;margin:0;padding:0}
html,body{width:1200px;height:3136px;overflow:hidden}
body{font-family:"Open Sans",Arial,sans-serif;color:var(--text);background:var(--white);position:relative}
section,header,footer{position:absolute;left:0;width:1200px}
.abs{position:absolute}
.center{text-align:center}
.section-title{position:absolute;left:0;width:1200px;text-align:center;font-size:23px;font-weight:700;color:var(--brown);letter-spacing:.5px}
.section-title.dark{color:#333}
.lede{position:absolute;left:0;width:1200px;text-align:center;font-size:14.5px;color:var(--muted)}
.btn{position:absolute;background:var(--tan);color:var(--white);font-size:13px;font-weight:700;letter-spacing:.8px;display:flex;align-items:center;justify-content:center;text-transform:uppercase}

/* nav */
.site-nav{top:0;height:70px;background:var(--white)}
.nav-link{position:absolute;top:26px;font-size:13.5px;font-weight:600;color:#222;text-transform:uppercase}
.nav-link.active{color:var(--brown)}
.brand{position:absolute;left:524px;top:0;width:152px;height:132px;background:var(--white);z-index:3;display:flex;flex-direction:column;align-items:center;padding-top:14px}
.brand-dot{width:52px;height:52px;border-radius:50%;background:var(--brown)}
.brand-name{margin-top:8px;font-size:12px;font-weight:600;color:var(--brown);text-align:center;line-height:1.25;letter-spacing:1px;text-transform:uppercase}
.social-link{position:absolute;right:75px;top:26px;font-size:13px;font-weight:600;color:var(--brown)}

/* hero */
.hero{top:70px;height:438px}
.hero-photo{position:absolute;inset:0;background:linear-gradient(120deg,#4a4038 0%,#6b5d52 35%,#8a8078 60%,#3f3a36 100%)}
.hero-title{position:absolute;left:75px;top:138px;font-size:46px;font-weight:700;color:var(--white);letter-spacing:1px}
.hero-sub{position:absolute;left:75px;top:192px;width:620px;font-size:26px;font-weight:600;color:var(--white);line-height:1.2}
.dots{position:absolute;display:flex;gap:7px}
.dots span{width:10px;height:10px;border-radius:50%;background:var(--white)}
.dots span.on{background:var(--tan)}
.quick{position:absolute;left:794px;top:45px;width:331px;height:349px;background:var(--white)}
.quick-head{height:48px;background:var(--brown);color:var(--white);font-size:24px;font-weight:700;display:flex;align-items:center;justify-content:center;letter-spacing:1px}
.field{position:absolute;left:19px;width:293px;height:36px;border:1px solid #aaa;font-size:12px;color:#666;padding:9px 14px}

/* welcome */
.welcome{top:508px;height:307px}
.welcome-copy{position:absolute;left:112px;top:92px;width:976px;text-align:center;font-size:14.5px;line-height:2.15;color:var(--muted)}

/* services */
.services{top:815px;height:456px;background:var(--soft)}
.service{position:absolute;top:152px;width:300px;text-align:center}
.service-icon{width:108px;height:108px;border:2px solid var(--brown);border-radius:50%;margin:0 auto;display:flex;align-items:center;justify-content:center}
.service h3,.member h3{margin-top:28px;font-size:16px;font-weight:700;color:var(--tan);letter-spacing:.5px}
.service p,.member p{margin-top:14px;font-size:14.5px;line-height:1.55;color:#444}

/* video */
.work{top:1271px;height:506px}
.video{position:absolute;left:253px;top:104px;width:694px;height:347px;background:linear-gradient(180deg,#5a4e48 0%,#7a3a3a 40%,#2f7a72 75%,#3c5860 100%)}
.play{position:absolute;left:318px;top:144px}

/* team */
.team{top:1777px;height:543px;background:var(--soft)}
.member{position:absolute;top:162px;width:240px;text-align:center}
.member-photo{width:240px;height:195px;background:linear-gradient(160deg,#d8d8d8,#9a9a9a)}
.member h3{margin-top:22px}
.member p{margin-top:12px;line-height:1.5}

/* news & reviews */
.updates{top:2320px;height:362px}
.col-title{position:absolute;top:46px;font-size:23px;font-weight:700;color:var(--brown)}
.divider{position:absolute;left:602px;top:46px;width:1px;height:270px;background:var(--line)}
.news-item{position:absolute;left:75px;width:500px}
.date{position:absolute;left:0;top:0;width:60px;height:76px}
.date-month{height:24px;background:var(--tan);color:var(--white);font-size:11px;font-weight:700;display:flex;align-items:center;justify-content:center}
.date-day{height:52px;background:var(--brown-dark);color:var(--white);font-size:30px;font-weight:700;display:flex;align-items:center;justify-content:center}
.news-body{position:absolute;left:88px;top:0;width:420px}
.news-body h4{font-size:14.5px;font-weight:700;color:var(--tan)}
.news-body p{margin-top:6px;font-size:14px;line-height:1.55;color:#444}
.news-body a{font-size:14px;color:var(--brown);text-decoration:none}
.quote-mark{position:absolute;left:631px;top:108px;width:46px;height:46px;border-radius:50%;background:var(--tan)}
.quote{position:absolute;left:690px;top:96px;width:435px;font-size:14px;font-style:italic;line-height:1.95;color:#444}
.quote-name{position:absolute;left:690px;top:203px;font-size:14px;color:var(--tan)}

/* press */
.press{top:2682px;height:171px;background:#f5f5f5}
.press-row{position:absolute;left:0;top:102px;width:1200px;display:flex;justify-content:center;gap:44px;font-size:17px;font-weight:700;color:#333}

/* footer */
.site-footer{top:2853px;height:224px}
.foot-head{position:absolute;top:40px;font-size:13.5px;font-weight:700;color:var(--brown);text-transform:uppercase}
.foot-list{position:absolute;top:72px;list-style:none;font-size:13.5px;line-height:30px;color:#444}
.email-field{position:absolute;left:884px;top:79px;width:241px;height:38px;border:1px solid #999;font-size:12.5px;color:#666;padding:10px 12px}
.copyright{top:3077px;height:59px;background:#e6e6e6;display:flex;align-items:center;justify-content:center;font-size:12.5px;color:#444}
</style>
</head>
<body>

<header class="site-nav">
  <span class="nav-link active" style="left:75px">Home</span>
  <span class="nav-link" style="left:151px">About Us</span>
  <span class="nav-link" style="left:255px">Services</span>
  <span class="nav-link" style="left:352px">Clients</span>
  <span class="nav-link" style="left:441px">Blog</span>
  <div class="brand">
    <div class="brand-dot"></div>
    <div class="brand-name">The Copperline<br>Collective</div>
  </div>
  <span class="nav-link" style="left:702px">News &amp; Events</span>
  <span class="nav-link" style="left:845px">Reviews</span>
  <span class="nav-link" style="left:937px">Contact Us</span>
  <span class="social-link">chatterbook</span>
</header>

<section class="hero">
  <div class="hero-photo" role="img" aria-label="Photo of a furniture store showroom with sofas and tables"></div>
  <h1 class="hero-title">COPPERLINE COLLECTIVE</h1>
  <p class="hero-sub">We are a promotional company that runs events for furniture stores to increase sales for short periods of time.</p>
  <div class="dots" style="left:75px;top:382px"><span class="on"></span><span></span><span></span><span></span></div>
  <form class="quick">
    <div class="quick-head">QUICK CONTACT</div>
    <div class="field" style="top:62px">Enter Name</div>
    <div class="field" style="top:107px">Enter Email Address</div>
    <div class="field" style="top:152px">Phone No</div>
    <div class="field" style="top:197px;height:84px">Message</div>
    <div class="btn" style="left:19px;top:294px;width:293px;height:42px">Submit</div>
  </form>
</section>

<section class="welcome">
  <h2 class="section-title" style="top:46px">WELCOME TO OUR WEBSITE</h2>
  <p class="welcome-copy">Aliquam molestie, mi et imperdiet euismod, dui purus auctor tellus, et interdum lacus lectus et ante. Sed accumsan sollicitudin sapien, sit amet adipiscing turpis gravida ac. In congue, neque ac lobortis volutpat, libero mauris varius mi, vitae suscipit ipsum ligula vitae risus. Duis aliquam nibh a dui iaculis viverra id a velit. Vivamus egestas risus in magna varius commodo. Sed semper viverra egestas.</p>
  <div class="btn" style="left:510px;top:207px;width:180px;height:48px">Read More</div>
</section>

<section class="services">
  <h2 class="section-title" style="top:48px">OUR SERVICES</h2>
  <p class="lede" style="top:96px">Aliquam molestie, mi et imperdiet euismod, dui purus auctor tellus, et interdum lacus lectus et ante.</p>
  <div class="service" style="left:90px">
    <div class="service-icon">
      <svg width="54" height="40" viewBox="0 0 54 40" fill="none" stroke="#8b5a2b" stroke-width="3"><rect x="10" y="4" width="34" height="18" rx="4"/><rect x="2" y="14" width="10" height="20" rx="3"/><rect x="42" y="14" width="10" height="20" rx="3"/><rect x="12" y="22" width="30" height="12"/><line x1="7" y1="34" x2="7" y2="39"/><line x1="47" y1="34" x2="47" y2="39"/></svg>
    </div>
    <h3>SERVICE HEADING</h3>
    <p>Sed accumsan sollicitudin sapien,<br>sit amet adipiscing turpis volutpat, libero<br>mauris varius mi, vitae suscipit ipsum<br>ligula vitae risus.</p>
  </div>
  <div class="service" style="left:450px">
    <div class="service-icon">
      <svg width="48" height="48" viewBox="0 0 48 48" fill="none" stroke="#8b5a2b" stroke-width="3"><path d="M4 6 L22 4 L44 26 L26 44 L4 22 Z"/><circle cx="14" cy="14" r="3.5"/></svg>
    </div>
    <h3>SERVICE HEADING</h3>
    <p>Sed accumsan sollicitudin sapien,<br>sit amet adipiscing turpis volutpat, libero<br>mauris varius mi, vitae suscipit ipsum<br>ligula vitae risus.</p>
  </div>
  <div class="service" style="left:809px">
    <div class="service-icon">
      <svg width="44" height="46" viewBox="0 0 44 46" fill="none" stroke="#8b5a2b" stroke-width="3"><rect x="3" y="7" width="38" height="36" rx="3"/><line x1="3" y1="16" x2="41" y2="16"/><line x1="12" y1="2" x2="12" y2="10"/><line x1="32" y1="2" x2="32" y2="10"/><g fill="#8b5a2b" stroke="none"><rect x="9" y="21" width="6" height="5"/><rect x="19" y="21" width="6" height="5"/><rect x="29" y="21" width="6" height="5"/><rect x="9" y="30" width="6" height="5"/><rect x="19" y="30" width="6" height="5"/><rect x="29" y="30" width="6" height="5"/></g></svg>
    </div>
    <h3>SERVICE HEADING</h3>
    <p>Sed accumsan sollicitudin sapien,<br>sit amet adipiscing turpis volutpat, libero<br>mauris varius mi, vitae suscipit ipsum<br>ligula vitae risus.</p>
  </div>
</section>

<section class="work">
  <h2 class="section-title" style="top:48px">WATCH HOW WE WORK</h2>
  <div class="video" role="img" aria-label="Video still: illustrated furniture showroom with shoppers and sale signs">
    <svg class="play" width="58" height="58" viewBox="0 0 58 58"><circle cx="29" cy="29" r="27" fill="#fff"/><circle cx="29" cy="29" r="20" fill="#222"/><path d="M24 19 L39 29 L24 39 Z" fill="#fff"/></svg>
  </div>
</section>

<section class="team">
  <h2 class="section-title dark" style="top:58px">ABOUT OUR TEAM</h2>
  <p class="lede" style="top:104px">Aliquam molestie, mi et imperdiet euismod, dui purus auctor tellus, et interdum lacus lectus et ante.</p>
  <div class="member" style="left:75px">
    <div class="member-photo" role="img" aria-label="Portrait photo of a senior team member"></div>
    <h3>NAME HEADING</h3>
    <p>Sed accumsan sollicitudin sapien,<br>sit amet adipiscing turpis volutpat,<br>libero mauris varius..</p>
  </div>
  <div class="member" style="left:344px">
    <div class="member-photo" role="img" aria-label="Portrait photo of a team member"></div>
    <h3>NAME HEADING</h3>
    <p>Sed accumsan sollicitudin sapien,<br>sit amet adipiscing turpis volutpat,<br>libero mauris varius..</p>
  </div>
  <div class="member" style="left:614px">
    <div class="member-photo" role="img" aria-label="Portrait photo of a team member"></div>
    <h3>NAME HEADING</h3>
    <p>Sed accumsan sollicitudin sapien,<br>sit amet adipiscing turpis volutpat,<br>libero mauris varius..</p>
  </div>
  <div class="member" style="left:885px">
    <div class="member-photo" role="img" aria-label="Portrait photo of a team member"></div>
    <h3>NAME HEADING</h3>
    <p>Sed accumsan sollicitudin sapien,<br>sit amet adipiscing turpis volutpat,<br>libero mauris varius..</p>
  </div>
</section>

<section class="updates">
  <h2 class="col-title" style="left:75px">NEWS &amp; EVENTS</h2>
  <article class="news-item" style="top:98px">
    <div class="date"><div class="date-month">AUG</div><div class="date-day">14</div></div>
    <div class="news-body">
      <h4>VESTIBULUM VEL METUS SIT AMET TURPIS..</h4>
      <p>Sed accumsan sollicitudin sapien, sit amet adipiscing turpis volutpat, libero mauris varius..</p>
      <a>Read More</a>
    </div>
  </article>
  <article class="news-item" style="top:215px">
    <div class="date"><div class="date-month">AUG</div><div class="date-day">14</div></div>
    <div class="news-body">
      <h4>VESTIBULUM VEL METUS SIT AMET TURPIS..</h4>
      <p>Sed accumsan sollicitudin sapien, sit amet adipiscing turpis volutpat, libero mauris varius..</p>
      <a>Read More</a>
    </div>
  </article>
  <div class="divider"></div>
  <h2 class="col-title" style="left:631px">CLIENTS REVIEWS</h2>
  <div class="dots" style="left:1078px;top:57px"><span style="background:var(--brown)"></span><span style="background:#999"></span><span style="background:#999"></span></div>
  <div class="quote-mark">
    <svg width="46" height="46" viewBox="0 0 46 46"><g fill="#fff"><rect x="15" y="17" width="6" height="6"/><path d="M21 23 L17 30 L15 30 L18 23 Z"/><rect x="25" y="17" width="6" height="6"/><path d="M31 23 L27 30 L25 30 L28 23 Z"/></g></svg>
  </div>
  <p class="quote">" Aliquam molestie, mi et imperdiet euismod, dui purus auctor tellus, et interdum lacus lectus et ante. Sed accumsan sollicitudin sapien, sit amet adipiscing turpis gravida ac lobortis turpis in odio blandit ac interdum lorem euismod.."</p>
  <span class="quote-name">-NAME HEADING</span>
  <div class="btn" style="left:631px;top:244px;width:180px;height:48px">Read All Reviews</div>
</section>

<section class="press">
  <h2 class="section-title" style="top:48px">AS SEEN ON</h2>
  <div class="press-row">
    <span>Westbay Trade Journal</span>
    <span>Ledgerline</span>
    <span>Channel North</span>
    <span>Market Pulse</span>
    <span>ByteWire</span>
    <span>Harbor City Times</span>
  </div>
</section>

<footer class="site-footer">
  <h4 class="foot-head" style="left:75px">Quick Links</h4>
  <ul class="foot-list" style="left:75px"><li>Home</li><li>About Us</li><li>Services</li><li>Clients</li></ul>
  <ul class="foot-list" style="left:215px"><li>Blog</li><li>Reviews</li><li>Contact Us</li></ul>
  <h4 class="foot-head" style="left:385px">Resources</h4>
  <ul class="foot-list" style="left:385px"><li>Vestibulum ante</li><li>Ipsum primis</li><li>Faucibus orci luctus</li><li>Ultrices posuere</li></ul>
  <h4 class="foot-head" style="left:615px">Contact Us</h4>
  <ul class="foot-list" style="left:615px;line-height:20px"><li>412 Alder Lane</li><li>Brookhaven, BR7 2QT</li><li style="margin-top:10px">1-800-555-0148</li><li style="margin-top:6px">hello@copperline.example</li></ul>
  <h4 class="foot-head" style="left:884px">Email Sign Up</h4>
  <div class="email-field">Enter Email Address</div>
  <div class="btn" style="left:1037px;top:130px;width:88px;height:40px">Sign Up</div>
</footer>

<div class="copyright" style="position:absolute;left:0;width:1200px">Copyright © 2017. The Copperline Collective. All Right Reserved</div>

</body>
</html>
```